A start-up named "Corvane Therapeutics" - needs a new PowerPoint design

We need a new PowerPoint Design for an early-stage start-up named "Corvane Therapeutics" seeking to disrupt the current approach towards drug discovery within aging disorders.

We would like to build on Corvane's legacy, the founder of the modern science of genetics, by employing a multidisciplinary approach, experimenting, and providing elderly patients the attention they deserve.

We have selected the suffix "therapeutics" intentionally as it stands for (a medicine) the treatment of disease; the science of healing. Alzheimer’s treatment is a huge, urgent, unmet need:
- Shift from a disease-management system to a preventive medicine system
- Focus on increasing the health span, not only the life span

Target Market(s)

Pharma/ Biotech Executives Medical Institutions Healthcare professionals (MDs, nurses, payors, pharmacists, etc.) Patients

Industry/Entity Type

Healthcare

Other font styles liked:
• Celias

Colors
0054AA
0677BA
7BADD7
CADEEF
E8F1F8
E54698
E96AAD
F1A4CE
F9D9EA
FCEFF6
A7469A
B969AE
D3A5CF
EDDBEB
F8F0F9
6B429C
8869AF
B7A5CE
E3DAEB
F3F0F8

Requirements
Must have
• - differentiate from other companies named after Corvane - differentiate from other Pharma/ Biotech companies
Nice to have
• simplicity/ minimalist logo vivid colors gradient 3D Life-Sciences inspired Simple geometry Balance
Should not have
• mascot/ emblem watermark logo animated ink style nature-inspired inventive typography artistic chaos

```html
<!DOCTYPE html>
<html lang="en">
<head>
<meta charset="utf-8">
<title>Corvane Therapeutics – Presentation Template Part 2</title>
<link href="https://fonts.googleapis.com/css2?family=Outfit:wght@400;500;600;700&family=Arimo:wght@700&display=swap" rel="stylesheet">
<style>
:root{
  --page:#f2f2f2;
  --dark:#262626;
  --white:#ffffff;
  --ink:#1d1d1d;
  --blue:#0054aa;
  --blue-mid:#0677ba;
  --cyan:#0a9bd8;
  --pink:#e54698;
  --purple:#3b1a56;
  --violet:#6b429c;
  --yellow:#e6ae3a;
  --green:#8dc63f;
  --orange:#f26b1d;
  --grid-dark:#5a5a5a;
  --grid-light:#d4d4d4;
}
*{box-sizing:border-box;margin:0;padding:0}
html,body{width:1200px;height:1200px;overflow:hidden;background:var(--page)}
body{position:relative;font-family:"Outfit",sans-serif;color:var(--ink)}
.slide{position:absolute;width:528px;height:297px;overflow:hidden;background:var(--white)}
.slide.dark{background:var(--dark);color:var(--white)}
.col-left{left:48.5px}.col-right{left:620.5px}
.row-1{top:40px}.row-2{top:373px}.row-3{top:710px}
.abs{position:absolute}
.slide-title{position:absolute;left:17px;top:18px;font-size:18px;font-weight:600;letter-spacing:.2px;color:var(--blue)}
.dark .slide-title{color:var(--pink)}
.brand{position:absolute;right:17px;top:19px;display:flex;align-items:center;gap:4px;font-size:12px;font-weight:500;color:var(--blue-mid)}
.brand-square{width:9px;height:9px;background:var(--violet)}
.footer-note{position:absolute;left:17px;bottom:9px;font-size:5.3px}
.page-tab{position:absolute;right:0;bottom:0;width:56px;height:20px}
.page-num{position:absolute;right:22px;bottom:6px;font-size:5px;font-weight:600;color:var(--white)}
/* agenda */
.agenda-item{position:absolute;display:flex;align-items:center;gap:11px}
.agenda-num{font-size:27px;font-weight:600;width:36px;text-align:center;line-height:1}
.agenda-text h3{font-size:8.6px;font-weight:600;margin-bottom:2px}
.agenda-text p{font-size:5.8px;line-height:1.35}
.v-divider{position:absolute;width:.7px;background:#666}
/* team */
.member{position:absolute;top:68px;width:99px;text-align:center}
.member .photo{width:99px;height:99px}
.member h3{margin-top:11px;font-size:9.3px;font-weight:600}
.member h4{font-size:8.2px;font-weight:600;margin-top:1px}
.member p{font-size:7.8px;line-height:1.2;margin-top:2px}
/* text blocks */
.text-block h3{font-size:11.5px;font-weight:600;margin-bottom:2px}
.text-block p{font-size:8.6px;line-height:1.22}
/* services */
.service{position:absolute;top:59px;width:119px;height:155px;color:var(--white);text-align:center}
.service svg{position:absolute;left:43px;top:19px}
.service .rule{position:absolute;left:10px;right:10px;top:71px;height:.7px;background:rgba(255,255,255,.55)}
.service h3{position:absolute;top:82px;width:100%;font-size:11.3px;font-weight:600}
.service p{position:absolute;top:99px;left:8px;right:8px;font-size:8.5px;line-height:1.25}
.service-band{position:absolute;left:0;right:0;top:227px;height:34px;background:var(--page);display:flex;align-items:center;justify-content:center;text-align:center;padding:0 20px;font-size:7.7px;font-weight:600;line-height:1.25}
svg text{font-family:"Outfit",sans-serif}
.part-label{position:absolute;left:46px;top:1040px;font-family:"Arimo",sans-serif;font-weight:700;font-size:113px;letter-spacing:1px;color:#000;line-height:1}
</style>
</head>
<body>

<!-- Agenda -->
<section class="slide dark col-left row-1">
  <h2 class="slide-title">Agenda Slide</h2>
  <div class="brand"><span class="brand-square"></span>Corvane</div>
  <div class="v-divider" style="left:264px;top:66px;height:188px"></div>
  <div class="agenda-item" style="left:24px;top:75px"><span class="agenda-num" style="color:var(--blue-mid)">01</span><div class="agenda-text"><h3>Section Header</h3><p>Lorem ipsum dolor sit amet, consectetur<br>adipiscing elit. Curabitur at fringilla velit.</p></div></div>
  <div class="agenda-item" style="left:24px;top:140px"><span class="agenda-num" style="color:var(--yellow)">02</span><div class="agenda-text"><h3>Section Header</h3><p>Lorem ipsum dolor sit amet, consectetur<br>adipiscing elit. Curabitur at fringilla velit.</p></div></div>
  <div class="agenda-item" style="left:24px;top:204px"><span class="agenda-num" style="color:var(--pink)">03</span><div class="agenda-text"><h3>Section Header</h3><p>Lorem ipsum dolor sit amet, consectetur<br>adipiscing elit. Curabitur at fringilla velit.</p></div></div>
  <div class="agenda-item" style="left:300px;top:75px"><span class="agenda-num" style="color:var(--green)">04</span><div class="agenda-text"><h3>Section Header</h3><p>Lorem ipsum dolor sit amet, consectetur<br>adipiscing elit. Curabitur at fringilla velit.</p></div></div>
  <div class="agenda-item" style="left:300px;top:140px"><span class="agenda-num" style="color:var(--cyan)">05</span><div class="agenda-text"><h3>Section Header</h3><p>Lorem ipsum dolor sit amet, consectetur<br>adipiscing elit. Curabitur at fringilla velit.</p></div></div>
  <div class="agenda-item" style="left:300px;top:204px"><span class="agenda-num" style="color:var(--orange)">06</span><div class="agenda-text"><h3>Section Header</h3><p>Lorem ipsum dolor sit amet, consectetur<br>adipiscing elit. Curabitur at fringilla velit.</p></div></div>
  <p class="footer-note">Copywrite Statement 2022</p>
  <svg class="page-tab" viewBox="0 0 56 20"><polygon points="10,0 15,0 5,20 0,20" fill="var(--pink)"/><polygon points="15,0 56,0 56,20 5,20" fill="var(--purple)"/></svg>
  <span class="page-num">7</span>
</section>

<!-- Team -->
<section class="slide col-right row-1">
  <h2 class="slide-title">Meet Our Team</h2>
  <div class="brand"><span class="brand-square"></span>Corvane</div>
  <div class="member" style="left:17px"><div class="photo" role="img" aria-label="Portrait photo of team member" style="background:linear-gradient(160deg,#6f8a3d,#c9b79a)"></div><h3 style="color:var(--blue-mid)">Enter Name Here</h3><h4>Position Title</h4><p>Lorem ipsum dolor sit amet, consectetur adipiscing elit</p></div>
  <div class="member" style="left:149px"><div class="photo" role="img" aria-label="Portrait photo of team member" style="background:linear-gradient(160deg,#e4e6e8,#9aa7b4)"></div><h3 style="color:var(--yellow)">Enter Name Here</h3><h4>Position Title</h4><p>Lorem ipsum dolor sit amet, consectetur adipiscing elit</p></div>
  <div class="member" style="left:281px"><div class="photo" role="img" aria-label="Portrait photo of team member" style="background:linear-gradient(160deg,#c9ccd0,#3f6fb5)"></div><h3 style="color:var(--purple)">Enter Name Here</h3><h4>Position Title</h4><p>Lorem ipsum dolor sit amet, consectetur adipiscing elit</p></div>
  <div class="member" style="left:413px"><div class="photo" role="img" aria-label="Portrait photo of team member" style="background:linear-gradient(160deg,#eeeeee,#1aa3b5)"></div><h3 style="color:var(--cyan)">Enter Name Here</h3><h4>Position Title</h4><p>Lorem ipsum dolor sit amet, consectetur adipiscing elit</p></div>
  <p class="footer-note">Copywrite Statement 2022</p>
  <svg class="page-tab" viewBox="0 0 56 20"><polygon points="10,0 15,0 5,20 0,20" fill="var(--pink)"/><polygon points="15,0 56,0 56,20 5,20" fill="var(--purple)"/></svg>
  <span class="page-num">8</span>
</section>

<!-- Chart with content -->
<section class="slide col-left row-2">
  <h2 class="slide-title">Chart with Content</h2>
  <div class="brand"><span class="brand-square"></span>Corvane</div>
  <div class="text-block abs" style="left:17px;top:71px;width:225px"><h3 style="color:var(--blue)">Section Header</h3><p>Donec vel suscipit purus, ultrices ornare neque. Sed nec est a lacus lacinia venenatis non at est. Vestibulum vitae lorem lectus. Phasellus gravida mauris a sapien elementum malesuada. Vestibulum ut urna eu dolor.</p></div>
  <div class="abs" style="left:17px;top:153px;width:224px;height:.7px;background:var(--grid-light)"></div>
  <div class="text-block abs" style="left:17px;top:167px;width:225px"><h3 style="color:var(--purple)">Section Header</h3><p>Lorem ipsum dolor sit amet, consectetur adipiscing elit. Curabitur at fringilla velit. In ac sagittis nulla. Nulla quis erat et ligula aliquam sagittis in viverra mauris. Pellentesque pharetra hendrerit orci at.</p></div>
  <div class="abs" style="left:273px;top:61px;width:.7px;height:200px;background:var(--grid-light)"></div>
  <svg class="abs" style="left:273px;top:60px" width="255" height="200" viewBox="0 0 255 200">
    <text x="121" y="16" text-anchor="middle" font-size="10" font-weight="600" fill="var(--blue)">Sales</text>
    <g transform="translate(121,99) rotate(-90)" fill="none" stroke-width="21">
      <circle r="62.5" stroke="var(--blue)" stroke-dasharray="227.8 392.7"/>
      <circle r="62.5" stroke="var(--purple)" stroke-dasharray="90.3 392.7" stroke-dashoffset="-227.8"/>
      <circle r="62.5" stroke="var(--yellow)" stroke-dasharray="39.3 392.7" stroke-dashoffset="-318.1"/>
      <circle r="62.5" stroke="var(--pink)" stroke-dasharray="35.3 392.7" stroke-dashoffset="-357.4"/>
    </g>
    <g font-size="7.2" fill="#444">
      <rect x="45" y="182" width="3.5" height="3.5" fill="var(--blue)"/><text x="51" y="186">1st Qtr</text>
      <rect x="83" y="182" width="3.5" height="3.5" fill="var(--purple)"/><text x="89" y="186">2nd Qtr</text>
      <rect x="123" y="182" width="3.5" height="3.5" fill="var(--yellow)"/><text x="129" y="186">3rd Qtr</text>
      <rect x="161" y="182" width="3.5" height="3.5" fill="var(--pink)"/><text x="167" y="186">4th Qtr</text>
    </g>
  </svg>
  <p class="footer-note">Copywrite Statement 2022</p>
  <svg class="page-tab" viewBox="0 0 56 20"><polygon points="10,0 15,0 5,20 0,20" fill="var(--pink)"/><polygon points="15,0 56,0 56,20 5,20" fill="var(--purple)"/></svg>
  <span class="page-num">9</span>
</section>

<!-- Stacked bar -->
<section class="slide dark col-right row-2">
  <h2 class="slide-title">Stacked Bar Style</h2>
  <div class="brand"><span class="brand-square"></span>Corvane</div>
  <div class="text-block abs" style="left:17px;top:61px;width:145px"><h3 style="color:var(--cyan)">Section Header</h3><p>Donec vel suscipit purus, ultrices ornare neque. Sed nec est a lacus lacinia venenatis non at est. Vestibulum vitae lorem lectus. Phasellus gravida mauris a sapien elementum malesuada. Vestibulum ut urna eu dolor.</p><p style="margin-top:10px">Lorem ipsum dolor sit amet, consectetur adipiscing elit. Curabitur at fringilla velit. In ac sagittis nulla. Nulla quis erat et ligula aliquam sagittis in viverra mauris. Pellentesque pharetra hendrerit orci at.</p></div>
  <svg class="abs" style="left:0;top:0" width="528" height="297" viewBox="0 0 528 297">
    <text x="342" y="75" text-anchor="middle" font-size="10" font-weight="600" fill="var(--pink)">Chart Title</text>
    <g stroke="var(--grid-dark)" stroke-width=".6">
      <line x1="236" y1="83" x2="236" y2="229"/><line x1="277.7" y1="83" x2="277.7" y2="229"/><line x1="319.3" y1="83" x2="319.3" y2="229"/><line x1="361" y1="83" x2="361" y2="229"/><line x1="402.7" y1="83" x2="402.7" y2="229"/><line x1="444.3" y1="83" x2="444.3" y2="229"/><line x1="486" y1="83" x2="486" y2="229"/>
    </g>
    <g>
      <rect x="236" y="87.6" width="208.5" height="7.5" fill="var(--cyan)"/><rect x="236" y="98.1" width="116.7" height="7.5" fill="var(--yellow)"/><rect x="236" y="108.6" width="187.6" height="7.5" fill="var(--pink)"/>
      <rect x="236" y="124.2" width="125" height="7.5" fill="var(--cyan)"/><rect x="236" y="134.7" width="75" height="7.5" fill="var(--yellow)"/><rect x="236" y="145.2" width="145.9" height="7.5" fill="var(--pink)"/>
      <rect x="236" y="160.8" width="83.3" height="7.5" fill="var(--cyan)"/><rect x="236" y="171.3" width="183.4" height="7.5" fill="var(--yellow)"/><rect x="236" y="181.8" width="104.2" height="7.5" fill="var(--pink)"/>
      <rect x="236" y="197.5" width="83.3" height="7.5" fill="var(--cyan)"/><rect x="236" y="208" width="100" height="7.5" fill="var(--yellow)"/><rect x="236" y="218.5" width="179.2" height="7.5" fill="var(--pink)"/>
    </g>
    <g font-size="6.4" fill="var(--white)" text-anchor="end">
      <text x="229" y="104">Category 4</text><text x="229" y="140.6">Category 3</text><text x="229" y="177.2">Category 2</text><text x="229" y="213.9">Category 1</text>
    </g>
    <g font-size="6.4" fill="var(--white)" text-anchor="middle">
      <text x="236" y="240">0</text><text x="277.7" y="240">1</text><text x="319.3" y="240">2</text><text x="361" y="240">3</text><text x="402.7" y="240">4</text><text x="444.3" y="240">5</text><text x="486" y="240">6</text>
    </g>
    <g font-size="6.4" fill="var(--white)">
      <rect x="293" y="246" width="3.5" height="3.5" fill="var(--cyan)"/><text x="298.5" y="249.7">Series 3</text>
      <rect x="330" y="246" width="3.5" height="3.5" fill="var(--yellow)"/><text x="335.5" y="249.7">Series 2</text>
      <rect x="367" y="246" width="3.5" height="3.5" fill="var(--pink)"/><text x="372.5" y="249.7">Series 1</text>
    </g>
  </svg>
  <p class="footer-note">Copywrite Statement 2022</p>
  <svg class="page-tab" viewBox="0 0 56 20"><polygon points="10,0 15,0 5,20 0,20" fill="var(--pink)"/><polygon points="15,0 56,0 56,20 5,20" fill="var(--purple)"/></svg>
  <span class="page-num">10</span>
</section>

<!-- Column chart -->
<section class="slide dark col-left row-3">
  <h2 class="slide-title">Chart</h2>
  <div class="brand"><span class="brand-square"></span>Corvane</div>
  <svg class="abs" style="left:0;top:0" width="528" height="297" viewBox="0 0 528 297">
    <text x="264" y="72" text-anchor="middle" font-size="11" font-weight="600" fill="var(--white)">Chart Title</text>
    <g stroke="var(--grid-dark)" stroke-width=".6">
      <line x1="31" y1="82" x2="505" y2="82"/><line x1="31" y1="104.1" x2="505" y2="104.1"/><line x1="31" y1="126.3" x2="505" y2="126.3"/><line x1="31" y1="148.4" x2="505" y2="148.4"/><line x1="31" y1="170.6" x2="505" y2="170.6"/><line x1="31" y1="192.7" x2="505" y2="192.7"/><line x1="31" y1="214.9" x2="505" y2="214.9"/><line x1="31" y1="237" x2="505" y2="237"/>
    </g>
    <g font-size="7.5" fill="var(--white)" text-anchor="middle">
      <text x="22" y="85">7</text><text x="22" y="107">6</text><text x="22" y="129">5</text><text x="22" y="151">4</text><text x="22" y="173">3</text><text x="22" y="195">2</text><text x="22" y="217">1</text><text x="22" y="240">0</text>
    </g>
    <rect x="41.5" y="148.4" width="41" height="88.6" fill="var(--blue-mid)"/>
    <rect x="124.5" y="170.6" width="41" height="66.4" fill="var(--yellow)"/>
    <rect x="206.5" y="192.7" width="41" height="44.3" fill="var(--pink)"/>
    <rect x="288.5" y="170.6" width="41" height="66.4" fill="var(--green)"/>
    <rect x="371.5" y="104.1" width="41" height="132.9" fill="var(--cyan)"/>
    <rect x="453.5" y="148.4" width="41" height="88.6" fill="var(--orange)"/>
    <g font-size="8" fill="var(--white)" text-anchor="middle">
      <text x="62" y="144">4</text><text x="145" y="166">3</text><text x="227" y="188">2</text><text x="309" y="166">3</text><text x="392" y="100">6</text><text x="474" y="144">4</text>
    </g>
    <g font-size="7.3" fill="var(--white)">
      <rect x="139" y="253" width="3.5" height="3.5" fill="var(--blue-mid)"/><text x="145" y="257">Series 1</text>
      <rect x="181" y="253" width="3.5" height="3.5" fill="var(--yellow)"/><text x="187" y="257">Series 2</text>
      <rect x="225" y="253" width="3.5" height="3.5" fill="var(--pink)"/><text x="231" y="257">Series 3</text>
      <rect x="268" y="253" width="3.5" height="3.5" fill="var(--green)"/><text x="274" y="257">Series 4</text>
      <rect x="312" y="253" width="3.5" height="3.5" fill="var(--cyan)"/><text x="318" y="257">Series 5</text>
      <rect x="356" y="253" width="3.5" height="3.5" fill="var(--orange)"/><text x="362" y="257">Series 6</text>
    </g>
  </svg>
  <p class="footer-note">Copywrite Statement 2022</p>
  <svg class="page-tab" viewBox="0 0 56 20"><polygon points="10,0 15,0 5,20 0,20" fill="var(--pink)"/><polygon points="15,0 56,0 56,20 5,20" fill="var(--purple)"/></svg>
  <span class="page-num">11</span>
</section>

<!-- Medical services -->
<section class="slide col-right row-3">
  <h2 class="slide-title">Medical Services</h2>
  <div class="brand"><span class="brand-square"></span>Corvane</div>
  <div class="service" style="left:17px;background:var(--blue)">
    <svg width="34" height="38" viewBox="0 0 34 38" fill="none" stroke="#fff" stroke-width="1.6"><rect x="7" y="3" width="20" height="31" rx="1"/><circle cx="17" cy="11" r="4"/><path d="M17 9v4M15 11h4M11 20h12M11 24h12M11 28h8M5 8h4M5 14h4M5 20h4M5 26h4"/></svg>
    <div class="rule"></div><h3>Section Header</h3><p>Lorem ipsum dolor sit amet, consecteturat es adipiscing elit. Curabitur fringilla</p>
  </div>
  <div class="service" style="left:141px;background:var(--yellow)">
    <svg width="34" height="38" viewBox="0 0 34 38"><path d="M2 10h12l3 4h15v20H2z" fill="#222"/><path d="M6 10V5h13l5 5" fill="none" stroke="#222" stroke-width="2"/><path d="M14 20h6v-4h0M17 18v10M12 23h10" stroke="var(--yellow)" stroke-width="3"/></svg>
    <div class="rule"></div><h3 style="color:#222">Section Header</h3><p style="color:#222">Lorem ipsum dolor sit amet, consecteturat es adipiscing elit. Curabitur fringilla</p>
  </div>
  <div class="service" style="left:265px;background:var(--purple)">
    <svg width="34" height="38" viewBox="0 0 34 38"><rect x="1" y="10" width="30" height="13" rx="6.5" transform="rotate(-40 16 16)" fill="#fff"/><line x1="16" y1="7" x2="16" y2="26" stroke="var(--purple)" stroke-width="2" transform="rotate(-40 16 16)"/><circle cx="24" cy="26" r="8" fill="#fff" stroke="var(--purple)" stroke-width="1.5"/><line x1="24" y1="18" x2="24" y2="34" stroke="var(--purple)" stroke-width="1.8"/></svg>
    <div class="rule"></div><h3>Section Header</h3><p>Lorem ipsum dolor sit amet, consecteturat es adipiscing elit. Curabitur fringilla</p>
  </div>
  <div class="service" style="left:389px;background:var(--cyan)">
    <svg width="34" height="38" viewBox="0 0 34 38" fill="none" stroke="#fff" stroke-width="2.4"><path d="M14 3l6 4-6 10-6-4z" fill="#fff"/><path d="M20 16a9 9 0 0 1-6 15"/><path d="M6 35h22M11 31h12"/><circle cx="14" cy="22" r="2" fill="#fff"/></svg>
    <div class="rule"></div><h3>Section Header</h3><p>Lorem ipsum dolor sit amet, consecteturat es adipiscing elit. Curabitur fringilla</p>
  </div>
  <div class="service-band">Lorem ipsum dolor sit amet, consectetur adipiscing elit. Curabitur at fringilla velit. In ac sagittis nulla. Nulla quis erat et ligula aliquam sagittis in viverra mauris. Pellentesque pharetra hendrerit orci at. Phasellus gravida mauris.</div>
  <p class="footer-note">Copywrite Statement 2022</p>
  <svg class="page-tab" viewBox="0 0 56 20"><polygon points="10,0 15,0 5,20 0,20" fill="var(--pink)"/><polygon points="15,0 56,0 56,20 5,20" fill="var(--purple)"/></svg>
  <span class="page-num">12</span>
</section>

<div class="part-label">PART 2</div>

</body>
</html>
```